Website - add Lead Capture and Funnel Pages - New Fresh Design

For design: please recreate this landing page: https://brisklanehaul.net/pqrtx-cooperative-signup/
We need a fresh new look for our website brisklanehaul.net - currently in Divi, and possibly move to Elementor. We need new landing pages, funnel designs, and lead capture pages.

Prefer someone that has experience with Landing Pages and Lead Capture.

The target market is: Owner Operators of Trucking Companies. In other words, a person that owns an 18 wheeler truck to transport materials, that also drives it. These owners, need support, and we offer support to them in order to keep them compliant with Bureau of Freight Oversight regulations in the United States.

Target Market(s)

Truckers in the USA who own and drive for themselves 18 wheelers...

Industry/Entity Type

Business to Business Services, Trucking

Coding

Coded - Design and coding required

Number of Pages Required

5+ page

Font styles to use
Sans Serif

Colors
0054AA
0677BA
7BADD7
CADEEF
E8F1F8

Requirements
Must have
• Lead Pages, Lead Capture, Funnel Creation, On Page SEO using Rankwell Toolkit, Blog Page area, Clear Call to Actions, Mobile Friendly.
Nice to have
• Keep current color scheme, follow logo colors. Nice to have custom photography, and video explainers.

```html
<!DOCTYPE html>
<html lang="en">
<head>
<meta charset="utf-8">
<title>Brisklane Haul – Compliance Made Simple</title>
<link href="https://fonts.googleapis.com/css2?family=Montserrat:wght@500;600;700&family=Roboto:wght@400;500;700&display=swap" rel="stylesheet">
<style>
:root{
  --primary:#0054AA;
  --primary-dark:#003d7d;
  --accent:#0677BA;
  --sky:#7BADD7;
  --mist:#CADEEF;
  --ice:#E8F1F8;
  --ink:#1f2a36;
  --text:#4f5b67;
  --muted:#8793a0;
  --dark:#10294a;
  --darker:#0b1d36;
  --line:#dbe6f1;
  --white:#ffffff;
}
*{margin:0;padding:0;box-sizing:border-box}
html,body{width:1200px;height:5343px;overflow:hidden}
body{position:relative;background:var(--white);font-family:'Roboto',Arial,sans-serif;color:var(--text)}
.abs{position:absolute}
h1,h2,h3,h4,.mont{font-family:'Montserrat',Arial,sans-serif}

/* header */
.site-header{top:0;left:0;width:1200px;height:88px;background:var(--white);z-index:5}
.topbar{left:698px;top:0;width:388px;height:29px;background:var(--ice);display:flex;align-items:center;justify-content:space-around;font-size:11px;color:#3b4856}
.topbar span{display:flex;align-items:center;gap:6px}
.topbar i{width:15px;height:15px;border-radius:50%;background:var(--primary);display:inline-block}
.brand{left:93px;top:30px;display:flex;align-items:center;gap:8px;font-family:'Montserrat',sans-serif;font-weight:600;font-size:19px;letter-spacing:2px;color:var(--ink)}
.brand b{width:12px;height:12px;background:var(--primary);display:block}
.nav{top:56px;font-family:'Montserrat',sans-serif;font-size:10.5px;font-weight:500;color:var(--ink);letter-spacing:.3px}
.nav.active{border-bottom:2px solid var(--primary);padding-bottom:22px}
.login{left:939px;top:46px;width:139px;height:31px;background:var(--primary);color:#fff;font-family:'Montserrat',sans-serif;font-size:11px;font-weight:600;display:flex;align-items:center;justify-content:center;gap:6px}

/* hero */
.hero{top:88px;left:0;width:1200px;height:648px;background:linear-gradient(100deg,#0b1d36 0%,#163a63 45%,#3d6d9c 75%,#6d9bc6 100%);overflow:hidden}
.hero-road{left:0;top:380px;width:1200px;height:270px;background:linear-gradient(180deg,#1e3f66,#0a1a2f)}
.hero-truck{left:330px;top:170px;width:400px;height:250px;background:linear-gradient(180deg,#40648c,#24436a);opacity:.6}
.hero-diamond{left:585px;top:210px;width:210px;height:210px;background:var(--accent);transform:rotate(45deg)}
.hero-person{left:660px;top:25px;width:360px;height:560px;background:linear-gradient(180deg,#a9c4dc,#4f7398 55%,#25466b);border-radius:160px 160px 10px 10px}
.eyebrow{left:116px;top:238px;font-family:'Montserrat',sans-serif;font-size:23px;letter-spacing:3.5px;color:#fff;font-weight:500}
.hero-title{left:112px;top:268px;font-family:'Montserrat',sans-serif;font-weight:600;font-size:54px;line-height:60px;color:#fff}
.hero-title em{font-style:normal;color:var(--sky)}
.hero-sub{left:118px;top:398px;font-size:17px;line-height:27px;color:#fff}
.btn{display:flex;align-items:center;justify-content:center;font-family:'Montserrat',sans-serif;font-weight:600;font-size:11px;color:#fff;border-radius:22px;letter-spacing:.3px}
.btn-grey{left:116px;top:477px;width:186px;height:41px;background:#4c6886}
.btn-blue{left:307px;top:477px;width:180px;height:41px;background:var(--accent)}
.arrow{top:330px;width:30px;height:48px}

/* intro */
.sec-title{width:1200px;text-align:center;font-family:'Montserrat',sans-serif;font-weight:600;color:var(--ink);letter-spacing:.5px}
.sec-title em{font-style:normal;color:var(--primary);display:block}
.lead{width:1200px;text-align:center;font-size:17px;color:var(--text)}
.card{top:1001px;width:234px;height:277px;background:#fff;box-shadow:0 3px 16px rgba(0,60,120,.12);padding:0 36px}
.card .ico{width:64px;height:64px;border-radius:50%;background:var(--ice);margin-top:30px;display:flex;align-items:center;justify-content:center}
.card h3{font-size:16px;font-weight:600;color:var(--ink);margin-top:24px}
.card p{font-size:11px;line-height:17.5px;color:var(--text);margin-top:10px}
.card.feature{top:986px;height:309px;background:linear-gradient(135deg,var(--accent) 0%,var(--primary) 70%,var(--primary-dark) 100%)}
.card.feature .ico{background:var(--primary-dark)}
.card.feature h3,.card.feature p{color:#fff}

/* order */
.order{top:1407px;left:0;width:1200px;height:500px;background:var(--dark);clip-path:polygon(0 0,100% 0,100% 72%,0 92%)}
.order-stripe{left:0;top:1850px;width:240px;height:5px;background:var(--accent);transform:rotate(5deg);transform-origin:left}
.video-frame{left:234px;top:1582px;width:160px;height:120px;border-top:8px solid var(--accent);border-left:8px solid var(--accent)}
.video-shadow{left:252px;top:1600px;width:690px;height:412px;background:var(--mist)}
.video{left:242px;top:1590px;width:691px;height:412px;background:linear-gradient(135deg,#5f7f9f,#2c4869 60%,#152a44);display:flex;flex-direction:column;align-items:center;justify-content:center;color:#fff;font-family:'Montserrat',sans-serif;font-size:27px;letter-spacing:1px;line-height:34px;text-align:center}
.play{left:550px;top:1754px;width:74px;height:74px}

/* women owned */
.wbe-title{left:640px;top:2164px;font-family:'Montserrat',sans-serif;font-size:25px;font-weight:600;line-height:33px;color:var(--ink);letter-spacing:.5px}
.rule{left:642px;top:2276px;width:66px;height:3px;background:var(--primary)}
.wbe-text{left:640px;top:2302px;width:430px;font-size:17px;line-height:23px;color:var(--text)}
.btn-sq{left:642px;top:2400px;width:154px;height:40px;background:var(--primary);color:#fff;font-family:'Montserrat',sans-serif;font-size:11px;font-weight:600;display:flex;align-items:center;justify-content:center;box-shadow:3px 3px 0 var(--primary-dark)}

/* who we serve */
.serve{top:2580px;left:0;width:1200px;height:570px;background:linear-gradient(180deg,var(--ice),var(--mist) 60%,var(--ice))}
.serve-title{left:100px;top:2734px;font-size:30px;font-weight:600;color:var(--ink);letter-spacing:1px}
.serve-text{left:100px;top:2808px;width:360px;font-size:17px;line-height:27px;color:var(--text)}
.tile{display:flex;flex-direction:column;justify-content:flex-end;padding:0 28px 22px;color:#fff;font-family:'Montserrat',sans-serif;font-weight:600;font-size:16px;letter-spacing:.5px}
.tile-feature{left:518px;top:2651px;width:259px;height:188px;background:linear-gradient(135deg,var(--accent),var(--primary));justify-content:flex-start;padding-top:54px;box-shadow:0 6px 18px rgba(0,40,90,.25)}
.tile-feature small{font-family:'Roboto',sans-serif;font-weight:400;font-size:10.5px;line-height:13px;margin-top:8px;opacity:.92}
.tile-photo{background:linear-gradient(160deg,#9db7cf,#4d6c8c 60%,#233e5e)}

/* compliance */
.svc{width:253px;height:193px;text-align:center;padding:0 18px}
.svc svg{margin-top:24px}
.svc h4{font-family:'Roboto',sans-serif;font-size:13px;font-weight:700;color:var(--ink);margin-top:10px}
.svc p{font-size:10px;line-height:17px;color:var(--muted);margin-top:8px}
.svc.raised{background:#fff;box-shadow:0 4px 16px rgba(0,60,120,.12)}
.vline{width:1px;background:var(--line)}
.hline{height:1px;background:var(--line)}

/* news */
.news{top:3845px;left:0;width:1200px;height:605px;background:var(--ice)}
.news-title{left:120px;top:3900px;font-family:'Montserrat',sans-serif;font-size:29px;font-weight:600;color:var(--ink);letter-spacing:.5px}
.news-title em{color:var(--primary);font-style:normal}
.news-big{left:120px;top:3975px;width:481px;height:381px;background:linear-gradient(160deg,#d6e4f1 0%,#b5c8da 35%,#3f6f9e 55%,#2a4566 80%,#162a42);overflow:hidden}
.news-big .shade{left:0;top:220px;width:481px;height:161px;background:linear-gradient(180deg,rgba(0,0,0,0),rgba(5,20,40,.78))}
.tag{background:var(--primary);color:#fff;font-size:10px;font-weight:700;padding:5px 10px}
.tag.dark{background:#2c4666}
.news-sm{left:609px;width:446px;height:181px;background:#fff;display:flex}
.news-sm .img{width:216px;height:181px;background:linear-gradient(160deg,#a8bfd4,#5b7b9b 60%,#34506f)}
.news-sm .body{padding:18px 20px}
.news-sm h4{font-family:'Roboto',sans-serif;font-size:11px;font-weight:700;color:var(--ink);margin-top:14px}
.news-sm p{font-size:11.5px;line-height:20px;color:var(--muted);margin-top:6px}

/* quote */
.quote{top:4450px;left:0;width:1200px;height:499px;background:linear-gradient(180deg,var(--accent),var(--primary) 70%,var(--primary-dark))}
.quote-truck{left:600px;top:4450px;width:600px;height:499px;background:linear-gradient(90deg,rgba(0,0,0,0),rgba(0,20,50,.2))}
.field{background:#fff;border:1px solid var(--mist);font-size:12px;color:var(--muted);padding:14px 18px}
.send{left:504px;top:4835px;width:190px;height:44px;border:2px solid #fff;color:#fff;font-family:'Montserrat',sans-serif;font-size:13px;font-weight:600;display:flex;align-items:center;justify-content:center;letter-spacing:.5px}

/* footer */
.footer{top:4949px;left:0;width:1200px;height:319px;background:var(--darker)}
.fcol{top:5018px}
.fcol h4{font-size:14px;font-weight:600;color:#fff;letter-spacing:.5px;border-left:3px solid var(--sky);padding-left:20px;height:22px;line-height:22px}
.fcol .fb{padding-left:23px;margin-top:18px;font-size:9.5px;line-height:18.5px;color:#b4c6d8}
.fsep{width:1px;background:#1f3656;top:5010px;height:220px}
.office{display:flex;gap:12px;margin-bottom:18px}
.pin{width:20px;height:20px;flex:none}
.copyright{top:5268px;left:0;width:1200px;height:75px;background:#071426;color:#7f95ab;font-size:9.5px;text-align:center;line-height:75px}
</style>
</head>
<body>

<header class="abs site-header">
  <div class="abs topbar">
    <span><i></i>Toll Free 800-555-0147</span>
    <span><i></i>sales@brisklanehaul.net</span>
  </div>
  <div class="abs brand"><b></b>BRISKLANE HAUL</div>
  <a class="abs nav active" style="left:410px">OUR SERVICES</a>
  <a class="abs nav" style="left:526px">PQRTX COMPLIANCE</a>
  <a class="abs nav" style="left:678px">INDUSTIRES WE SERVE</a>
  <a class="abs nav" style="left:837px">CONTACT US</a>
  <div class="abs login">
    <svg width="12" height="12" viewBox="0 0 12 12"><circle cx="6" cy="3.5" r="2.8" fill="#fff"/><path d="M0.5 12c0-3.5 2.5-5 5.5-5s5.5 1.5 5.5 5z" fill="#fff"/></svg>
    Corporate Login
  </div>
</header>

<section class="abs hero">
  <div class="abs hero-road" role="img" aria-label="Highway at dusk"></div>
  <div class="abs hero-truck" role="img" aria-label="Semi truck on the highway"></div>
  <div class="abs hero-diamond"></div>
  <div class="abs hero-person" role="img" aria-label="Smiling truck driver in a cap and plaid shirt, arms crossed"></div>
  <div class="abs eyebrow">BRISKLANE HAUL</div>
  <h1 class="abs hero-title"><em>COMPLIANCE</em><br>MADE SIMPLE</h1>
  <p class="abs hero-sub">Pre-Employment Screening: Backgrounds -<br>Drug Testing - Driving Records.a</p>
  <a class="abs btn btn-grey">ORDER A REPORT</a>
  <a class="abs btn btn-blue">JOIN CONSORTIUM</a>
  <svg class="abs arrow" style="left:26px" viewBox="0 0 30 48"><path d="M24 4 6 24l18 20" fill="none" stroke="#fff" stroke-width="2.5"/></svg>
  <svg class="abs arrow" style="left:1142px" viewBox="0 0 30 48"><path d="M6 4l18 20L6 44" fill="none" stroke="#fff" stroke-width="2.5"/></svg>
  <svg class="abs" style="left:0;top:0" width="1200" height="648" viewBox="0 0 1200 648">
    <polygon points="0,530 436,648 0,648" fill="#ffffff"/>
    <polygon points="0,522 436,640 436,648 0,530" fill="#4c6886"/>
    <polygon points="436,648 1200,505 1200,648" fill="#ffffff"/>
    <polygon points="436,648 1200,478 1200,505 436,648" fill="#0677BA"/>
  </svg>
</section>

<h2 class="abs sec-title" style="top:814px;left:0;font-size:29px;line-height:40px">THE SMART &amp; AFFORDABLE APPROACH TO<em>EMPLOYMENT SCREENING</em></h2>
<p class="abs lead" style="top:906px;left:0">We take a complicated process and make it easy.</p>

<div class="abs card" style="left:114px">
  <div class="ico"><svg width="30" height="30" viewBox="0 0 30 30"><rect x="5" y="5" width="20" height="16" rx="2" fill="none" stroke="#0054AA" stroke-width="1.6"/><path d="M3 24h24" stroke="#0054AA" stroke-width="1.6"/><path d="M10 10h10M10 14h7" stroke="#0054AA" stroke-width="1.4"/></svg></div>
  <h3>Data Entry Free!</h3>
  <p>No more paper forms, data, or emails back and forth. All we need is the applicants email, we take care of the rest.</p>
</div>
<div class="abs card feature" style="left:356px">
  <div class="ico"><svg width="30" height="30" viewBox="0 0 30 30"><rect x="6" y="4" width="18" height="22" rx="2" fill="none" stroke="#fff" stroke-width="1.6"/><path d="M10 10h10M10 14h10M10 18h6" stroke="#fff" stroke-width="1.4"/></svg></div>
  <h3>FCRA Compliant</h3>
  <p>We make sure the process is FCRA compliant. Electronic Signatures, Consent Forms, Disclosure and Court Verifications.</p>
</div>
<div class="abs card" style="left:605px">
  <div class="ico"><svg width="30" height="30" viewBox="0 0 30 30"><circle cx="15" cy="12" r="6" fill="none" stroke="#0054AA" stroke-width="1.6"/><path d="M6 26c1-5 5-7 9-7s8 2 9 7" fill="none" stroke="#0054AA" stroke-width="1.6"/></svg></div>
  <h3>Simple Pricing</h3>
  <p>Whether you need a background on yourself or someone else, one report or multiple services, we offer affordable Nationwide Services 24/7.</p>
</div>
<div class="abs card" style="left:848px">
  <div class="ico"><svg width="30" height="30" viewBox="0 0 30 30"><rect x="5" y="6" width="20" height="14" rx="1.5" fill="none" stroke="#0054AA" stroke-width="1.6"/><path d="M2 23h26" stroke="#0054AA" stroke-width="1.6"/><path d="M9 11h12M9 15h8" stroke="#0054AA" stroke-width="1.4"/></svg></div>
  <h3>Online Reporting</h3>
  <p>Track applicant status, and get notifications about report status right to your email. View reports 24/7 in your Secure Dashboard.</p>
</div>

<section class="abs order"></section>
<div class="abs order-stripe"></div>
<h2 class="abs sec-title" style="top:1464px;left:0;font-size:33px;color:#fff;letter-spacing:1.5px">HOW TO ORDER HERE</h2>
<p class="abs lead" style="top:1519px;left:0;color:#fff">We take a complicated process and make it easy.</p>
<div class="abs video-frame"></div>
<div class="abs video-shadow"></div>
<div class="abs video" role="img" aria-label="Video thumbnail: woman working on a laptop in an office">
  <div style="margin-top:80px">REDUCE TIME TO HIRE<br>WITH AUTOMATED WORKFLOWS BETWEEN</div>
</div>
<svg class="abs play" viewBox="0 0 74 74"><circle cx="37" cy="37" r="33" fill="rgba(255,255,255,.15)" stroke="#fff" stroke-width="4"/><circle cx="37" cy="37" r="26" fill="#0054AA"/><polygon points="30,24 52,37 30,50" fill="#fff"/></svg>

<svg class="abs" style="left:120px;top:2108px" width="464" height="404" viewBox="0 0 464 404">
  <polygon points="116,2 348,2 462,202 348,402 116,402 2,202" fill="none" stroke="#0054AA" stroke-width="2"/>
  <defs><linearGradient id="hexfill" x1="0" y1="0" x2="1" y2="1"><stop offset="0" stop-color="#3a78b5"/><stop offset=".5" stop-color="#8fb1cf"/><stop offset="1" stop-color="#3f5e7d"/></linearGradient></defs>
  <polygon role="img" aria-label="Smiling woman driver in a blue cap at the wheel of a truck" points="130,26 334,26 436,202 334,378 130,378 28,202" fill="url(#hexfill)"/>
</svg>
<h2 class="abs wbe-title">BRISKLANE HAUL IS A WOMEN<br>OWNED, CERTIFIED WBE, MBE &amp;<br>DBE IN AZ, CA, TX &amp; NV</h2>
<div class="abs rule"></div>
<p class="abs wbe-text">Lorem ipsum dolor sit amet, consectetur adipiscing elit, sed do eiusmod tempor incididunt ut labore et dolore magna aliqua.</p>
<a class="abs btn-sq">CERTIFICATIONS</a>

<section class="abs serve" role="img" aria-label="Faint city skyline background"></section>
<h2 class="abs serve-title">WHO WE SERVE</h2>
<p class="abs serve-text">Lorem ipsum dolor sit amet, consectetur adipiscing elit, sed do eiusmod tempor incididunt ut labore et dolore magna aliqua Lorem ipsum dolor sit</p>
<div class="abs tile tile-feature">ENTREPRENEUR<small>We serve the Entrepreneur who wants to get the process started with the applicant and leaves the workflow up to us We serve the HR Manager</small></div>
<div class="abs tile tile-photo" style="left:518px;top:2848px;width:259px;height:190px" role="img" aria-label="Small business team meeting">SMALL BUSINESS</div>
<div class="abs tile tile-photo" style="left:790px;top:2705px;width:257px;height:190px" role="img" aria-label="Two colleagues shaking hands">SOLOPRENUER</div>
<div class="abs tile tile-photo" style="left:790px;top:2912px;width:257px;height:188px" role="img" aria-label="Smiling woman at her office desk">INDIVIDUAL</div>

<h2 class="abs sec-title" style="top:3215px;left:0;font-size:29px;line-height:34px">COMPLIANCE SERVICES FOR<em>MOTOR CARRIERS</em></h2>

<div class="abs vline" style="left:373px;top:3341px;height:389px"></div>
<div class="abs vline" style="left:621px;top:3341px;height:389px"></div>
<div class="abs vline" style="left:878px;top:3341px;height:389px"></div>
<div class="abs hline" style="left:118px;top:3536px;width:1007px"></div>

<div class="abs svc" style="left:118px;top:3341px">
  <svg width="44" height="44" viewBox="0 0 44 44"><rect x="8" y="6" width="28" height="32" rx="2" fill="none" stroke="#0054AA" stroke-width="1.8"/><path d="M13 14h18M13 20h18M13 26h12" stroke="#0054AA" stroke-width="1.6"/></svg>
  <h4>Clearinghouse Enrollment</h4>
  <p>PQRTX Clearinghouse launched Jan 2020 and many carriers have yet to enroll in the Clearinghouse. a</p>
</div>
<div class="abs svc raised" style="left:374px;top:3341px">
  <svg width="44" height="44" viewBox="0 0 44 44"><circle cx="20" cy="14" r="7" fill="none" stroke="#0054AA" stroke-width="1.8"/><path d="M8 36c1-8 6-11 12-11" fill="none" stroke="#0054AA" stroke-width="1.8"/><path d="M26 36l10-10 3 3-10 10h-3z" fill="none" stroke="#0054AA" stroke-width="1.6"/></svg>
  <h4>BOC3 Registration</h4>
  <p>BOC3 is required for each MC that has their own Authority. The BOC3 designates an Agent per State for</p>
</div>
<div class="abs svc" style="left:622px;top:3341px">
  <svg width="44" height="44" viewBox="0 0 44 44"><rect x="7" y="8" width="28" height="28" rx="3" fill="none" stroke="#0054AA" stroke-width="1.8"/><path d="M16 28l2-6 14-14 4 4-14 14z" fill="none" stroke="#0054AA" stroke-width="1.6"/></svg>
  <h4>IRP Registration</h4>
  <p>Registration reciprocity agreement among the US and Canadian Provinces, which provides payment of license fees</p>
</div>
<div class="abs svc" style="left:879px;top:3341px">
  <svg width="44" height="44" viewBox="0 0 44 44"><rect x="9" y="6" width="24" height="32" rx="2" fill="none" stroke="#0054AA" stroke-width="1.6"/><path d="M14 14h14M14 19h14M14 24h9" stroke="#0054AA" stroke-width="1.4"/><path d="M26 32l8-8 3 3-8 8h-3z" fill="none" stroke="#0054AA" stroke-width="1.4"/></svg>
  <h4>SCAC Registration</h4>
  <p>A registration code used to identify transportation companies doing business with military, government,</p>
</div>

<div class="abs svc" style="left:118px;top:3537px">
  <svg width="44" height="44" viewBox="0 0 44 44"><rect x="4" y="16" width="22" height="20" rx="2" fill="none" stroke="#0054AA" stroke-width="1.8"/><circle cx="30" cy="14" r="9" fill="none" stroke="#0054AA" stroke-width="1.8"/><path d="M28 11c0-2 4-2 4 0s-2 2-2 4M30 18v.5" fill="none" stroke="#0054AA" stroke-width="1.6"/></svg>
  <h4>Driver Clearinghouse Query</h4>
  <p>PQRTX Clearinghouse launched Jan 2020 and many carriers have yet to enroll in the Clearinghouse. a</p>
</div>
<div class="abs svc" style="left:374px;top:3537px">
  <svg width="44" height="44" viewBox="0 0 44 44"><rect x="8" y="6" width="28" height="32" rx="2" fill="none" stroke="#0054AA" stroke-width="1.8"/><circle cx="22" cy="18" r="6" fill="none" stroke="#0054AA" stroke-width="1.6"/><path d="M14 32h16" stroke="#0054AA" stroke-width="1.6"/></svg>
  <h4>UCR Registration</h4>
  <p>BOC3 is required for each MC that has their own Authority. The BOC3 designates an Agent per State for</p>
</div>
<div class="abs svc" style="left:622px;top:3537px">
  <svg width="44" height="44" viewBox="0 0 44 44"><rect x="9" y="6" width="24" height="32" rx="2" fill="none" stroke="#0054AA" stroke-width="1.8"/><path d="M14 14h14M14 20h14M14 26h10" stroke="#0054AA" stroke-width="1.6"/></svg>
  <h4>IFTA Registration</h4>
  <p>Registration reciprocity agreement among the US and Canadian Provinces, which provides payment of license fees</p>
</div>
<div class="abs svc" style="left:879px;top:3537px">
  <svg width="44" height="44" viewBox="0 0 44 44"><path d="M10 34l14-14M20 10l14 14M14 30l-4 4M28 8l8 8-4 4-8-8z" fill="none" stroke="#0054AA" stroke-width="1.8"/><circle cx="14" cy="14" r="5" fill="none" stroke="#0054AA" stroke-width="1.6"/></svg>
  <h4>Drug Testing Consortium</h4>
  <p>A registration code used to identify transportation companies doing business with military, government,</p>
</div>

<section class="abs news"></section>
<h2 class="abs news-title">LATEST <em>NEWS</em></h2>
<article class="abs news-big" role="img" aria-label="Semi truck parked in a truck yard">
  <div class="abs shade"></div>
</article>
<span class="abs tag" style="left:156px;top:4246px">28 MAY 2021</span>
<h3 class="abs mont" style="left:156px;top:4278px;width:420px;font-size:17px;line-height:21px;color:#fff;font-weight:600">Lorem ipsum dolor sit amet, consectetur ad-ipiscing elit, sed do eiusmod tempor</h3>

<article class="abs news-sm" style="top:3975px">
  <div class="img" role="img" aria-label="Driver seated in a truck cab"></div>
  <div class="body"><span class="tag dark">19 MAY 2021</span><h4>Lorem ipsum dolor sit</h4><p>Duis aute irure dolor in repre-henderit in voluptate velit esse cillum dolore eu fugiat</p></div>
</article>
<article class="abs news-sm" style="top:4172px">
  <div class="img" role="img" aria-label="Smiling woman driving a truck"></div>
  <div class="body"><span class="tag dark">18 MAY 2021</span><h4>Lorem ipsum dolor sit</h4><p>Duis aute irure dolor in repre-henderit in voluptate velit esse cillum dolore eu fugiat</p></div>
</article>

<section class="abs quote" role="img" aria-label="Semi truck background"></section>
<div class="abs quote-truck"></div>
<h2 class="abs sec-title" style="top:4545px;left:0;font-size:28px;color:#fff;letter-spacing:1px">REQUEST A QUOTE</h2>
<div class="abs field" style="left:267px;top:4615px;width:326px;height:44px">First Name</div>
<div class="abs field" style="left:601px;top:4615px;width:326px;height:44px">Last Name</div>
<div class="abs field" style="left:267px;top:4667px;width:326px;height:44px">Phone Number</div>
<div class="abs field" style="left:601px;top:4667px;width:326px;height:44px">Email address</div>
<div class="abs field" style="left:267px;top:4719px;width:660px;height:90px">Message</div>
<a class="abs send">SEND ENQUIRY</a>

<footer class="abs footer"></footer>
<div class="abs fsep" style="left:345px"></div>
<div class="abs fsep" style="left:570px"></div>
<div class="abs fsep" style="left:828px"></div>

<div class="abs fcol" style="left:102px;width:230px">
  <h4 class="mont">OUR OFFICE</h4>
  <div class="fb">
    <div class="office"><svg class="pin" viewBox="0 0 20 20"><circle cx="10" cy="10" r="10" fill="#fff"/><path d="M10 4a4 4 0 0 0-4 4c0 3 4 8 4 8s4-5 4-8a4 4 0 0 0-4-4z" fill="#0b1d36"/></svg><span>4100 Harbor Line Rd, Ste 2, Mesa,<br>AZ Florida Office</span></div>
    <div class="office"><svg class="pin" viewBox="0 0 20 20"><circle cx="10" cy="10" r="10" fill="#fff"/><path d="M10 4a4 4 0 0 0-4 4c0 3 4 8 4 8s4-5 4-8a4 4 0 0 0-4-4z" fill="#0b1d36"/></svg><span>880 Ridgecrest Way, Ste<br>14, Ocala, FL</span></div>
  </div>
</div>
<div class="abs fcol" style="left:362px;width:200px">
  <h4 class="mont">CONTACT US</h4>
  <div class="fb"><b style="color:#fff">Customer Inquiry</b><br>Toll Free: 800-555-0147<br>Phone: 602-555-0188<br>Fax: 602-555-0190<br>sales@brisklanehaul.net<br>consortium@brisklanehaul.net</div>
</div>
<div class="abs fcol" style="left:587px;width:230px">
  <h4 class="mont">QUICK LINKS</h4>
  <div class="fb">Drug Testing Needs Assessment<br>WorkCheck Client Sign-Up<br>WorkCheck – I9 Entry<br>Background Consent E-Form<br>Affiliate Referral Tracking<br>99 Drug Testing Clinics<br>Blog</div>
</div>
<div class="abs fcol" style="left:846px;width:240px">
  <h4 class="mont">PDF DOWNLOADS</h4>
  <div class="fb">Applicant Consent Form PDF<br>Applicant Consent Form Word<br>FCRA Summary of Rights</div>
</div>

<div class="abs copyright">© 2020 Brisklane Haul Background Checks &amp; Drug Testing</div>

</body>
</html>
```